Business Card for premium dental clinic

We are a premium dental clinic based in Brasov, Romania with more than 15 year on the market, providing quality dental treatment made by a team of more specialized dentists, working with modern equipment as a solution to beautiful and healthy teeth.

Our current logo for the clinic use 2 square with colors black and gold - dr Ternisu - studio, using family fonts Bodoni, Myriad Pro and Segoe Print.
Depending on the printing we used some gold CMYK background or gold foil picture background or a gold gradient.
We want a business card:
- eye catching business card
- distinguished business card
- premium design
- to keep the color scheme of black and gold
- to attract the customers to spent time reading the information
- modern concept

```html
<!DOCTYPE html>
<html lang="en">
<head>
<meta charset="utf-8">
<title>dr Ternisu studio – Business Card</title>
<link href="https://fonts.googleapis.com/css2?family=Lato:wght@400;700&family=Oswald:wght@400&display=swap" rel="stylesheet">
<style>
  :root {
    --gold: #b8892b;
    --ink: #111111;
    --paper: #ffffff;
    --rule: #a8a8a8;
    --backdrop: #e9e9e9;
  }
  html, body {
    margin: 0;
    padding: 0;
    width: 1200px;
    height: 1200px;
    overflow: hidden;
    background: var(--backdrop);
    font-family: "Lato", sans-serif;
    color: var(--ink);
  }
  .card {
    position: absolute;
    top: 310px;
    height: 594px;
    background: var(--paper);
    box-shadow: 0 1px 4px rgba(0,0,0,0.18);
  }
  .card--front { left: 234px; width: 364px; }
  .card--back { left: 627px; width: 369px; }

  .brand {
    position: absolute;
    display: flex;
    align-items: center;
    justify-content: center;
    gap: 14px;
  }
  .card--front .brand { left: 48px; top: 131px; width: 269px; height: 133px; }
  .card--back .brand { left: 52px; top: 120px; width: 266px; height: 130px; }
  .brand__square {
    width: 34px;
    height: 34px;
    background: var(--gold);
    flex: none;
  }
  .brand__name {
    font-family: "Lato", sans-serif;
    font-weight: 400;
    font-size: 30px;
    color: var(--ink);
    white-space: nowrap;
  }

  .centered {
    position: absolute;
    left: 0;
    width: 100%;
    text-align: center;
    margin: 0;
  }
  .person__name {
    top: 344px;
    font-weight: 700;
    font-size: 21px;
    color: var(--gold);
    letter-spacing: 0.2px;
  }
  .person__title { top: 366px; font-size: 17px; }

  .contact-icons {
    position: absolute;
    left: 0;
    top: 395px;
    width: 100%;
    height: 26px;
  }
  .contact__line { top: 431px; font-size: 17px; }
  .contact__line--mail { top: 453px; }
  .contact__line--web { top: 475px; }
  .divider {
    position: absolute;
    left: 88px;
    top: 507px;
    width: 195px;
    height: 1px;
    background: var(--rule);
  }
  .address__line { top: 518px; font-size: 17px; }
  .address__line--second { top: 540px; }

  .appointment__heading {
    position: absolute;
    left: 52px;
    top: 313px;
    width: 266px;
    margin: 0;
    font-family: "Oswald", sans-serif;
    font-weight: 400;
    font-size: 30px;
    text-align: center;
    letter-spacing: -0.5px;
    white-space: nowrap;
  }
  .field {
    position: absolute;
    left: 51px;
    width: 267px;
    font-size: 21px;
    border-bottom: 2px solid var(--rule);
    padding-bottom: 1px;
    line-height: 24px;
  }
  .field--name { top: 395px; }
  .field--time { top: 455px; }
  .notice { font-size: 17px; line-height: 23px; top: 512px; }
</style>
</head>
<body>

<section class="card card--front">
  <div class="brand">
    <span class="brand__square"></span>
    <span class="brand__name">dr Ternisu studio</span>
  </div>

  <p class="centered person__name">MARCUS HALE</p>
  <p class="centered person__title">Managing Director</p>

  <svg class="contact-icons" viewBox="0 0 364 26" aria-hidden="true">
    <line x1="87" y1="13" x2="138" y2="13" stroke="#a8a8a8" stroke-width="1.5"/>
    <line x1="224" y1="13" x2="277" y2="13" stroke="#a8a8a8" stroke-width="1.5"/>
    <circle cx="154" cy="13" r="12" fill="#b8892b"/>
    <circle cx="182" cy="13" r="12" fill="#b8892b"/>
    <circle cx="209" cy="13" r="12" fill="#b8892b"/>
    <!-- phone -->
    <path d="M148 15 h12 v3 h-12 z M147 12 q7 -6 14 0 l-2 2 h-10 z" fill="#fff"/>
    <!-- mail -->
    <rect x="175" y="8" width="14" height="10" fill="none" stroke="#fff" stroke-width="1.5"/>
    <path d="M175 8 l7 6 l7 -6" fill="none" stroke="#fff" stroke-width="1.5"/>
    <!-- globe -->
    <circle cx="209" cy="13" r="7" fill="none" stroke="#fff" stroke-width="1.5"/>
    <path d="M202 13 h14 M209 6 q-4 7 0 14 q4 -7 0 -14" fill="none" stroke="#fff" stroke-width="1.2"/>
  </svg>

  <p class="centered contact__line">044-987 321 650</p>
  <p class="centered contact__line contact__line--mail">hello@ternisustudio.com</p>
  <p class="centered contact__line contact__line--web">www.ternisustudio.com</p>
  <div class="divider"></div>
  <p class="centered address__line">17, Lindenpath Street,</p>
  <p class="centered address__line address__line--second">50021, Brightvale</p>
</section>

<section class="card card--back">
  <div class="brand">
    <span class="brand__square"></span>
    <span class="brand__name">dr Ternisu studio</span>
  </div>

  <h2 class="appointment__heading">YOUR NEXT APPOINTMENT</h2>
  <div class="field field--name">NAME</div>
  <div class="field field--time">TIME</div>
  <p class="centered notice">If unable to keep appointment<br>kindly give 24hrs notice.</p>
</section>

</body>
</html>
```